Bluefinch Painting needs a Website

We need a website built for a Painting company I own, we mainly do residential painting, but don't want to be limited to that.

Need to have estimate request form.
Need pic's of past projects

I like the look of the website for http://www.harbor-brushworks.com
& "Westlake Home inspections"

My logo that was designed here on ArtHatch on the front page

I would like one of the houses I downloaded as part of the background
of the front page.

Target Market(s)

Home owners

Industry/Entity Type

Painting

Number of Pages Required

1 page

Font styles to use
Serif

Requirements
Must have
• Estimate request form for home owners to fill out -
• Name:
• Phone Number:
• Address:
• E-mail:
• Painting project description:
• And my info to:
• My phone number: (555) 318-7046
• My web address bluefinchpainting.example
Nice to have
• My logo that was designed here on ArtHatch

```html
<!DOCTYPE html>
<html lang="en">
<head>
<meta charset="utf-8">
<title>Bluefinch Painting</title>
<link rel="stylesheet" href="https://fonts.googleapis.com/css2?family=Arimo:wght@400;700&family=Roboto+Condensed:wght@400;500&family=Roboto+Slab:wght@400;700&family=Vollkorn:wght@400;600&display=swap">
<style>
:root{
  --blue:#1b7fc6;
  --blue-dark:#0f5f9a;
  --ink:#1a1a1a;
  --muted:#333;
  --sky:#b8d7ec;
  --panel:#f2f2f2;
  --footer:#151515;
  --white:#fff;
  --field:rgba(235,235,235,.82);
}
*{box-sizing:border-box;margin:0;padding:0}
html,body{width:1200px;height:1015px;overflow:hidden;background:var(--white)}
body{position:relative;font-family:"Arimo",Arial,sans-serif;color:var(--ink)}
.abs{position:absolute}

/* header */
.site-header{position:absolute;left:0;top:0;width:1200px;height:116px;background:var(--white);border-bottom:1px solid #f0d6dc}
.brand{position:absolute;left:160px;top:46px;display:flex;align-items:center;gap:10px}
.brand-square{width:40px;height:40px;background:var(--blue)}
.brand-name{font-family:"Roboto Slab",serif;font-weight:400;font-size:27px;letter-spacing:2px;color:#111;line-height:1}
.estimate-btn{position:absolute;left:718px;top:17px;width:150px;height:28px;background:var(--blue);color:var(--white);font-family:"Roboto Condensed",sans-serif;font-size:19px;display:flex;align-items:center;justify-content:center}
.call{position:absolute;left:884px;top:15px;display:flex;gap:7px;align-items:center}
.call-text{line-height:1.1}
.call-label{font-size:14px;color:#333}
.call-number{font-size:19px;color:#222}
.main-nav{position:absolute;top:70px;left:590px;display:flex;font-size:13px;letter-spacing:.3px;color:#222}
.main-nav a{color:inherit;text-decoration:none;height:24px;display:flex;align-items:center}
.main-nav .current{background:var(--blue);color:var(--white);width:63px;justify-content:center;margin-right:20px}
.main-nav .item{margin-right:24px}

/* hero */
.hero{position:absolute;left:0;top:116px;width:1200px;height:397px;background:linear-gradient(180deg,#8e949a 0%,#6f7069 45%,#3f4a36 80%,#2f3a2a 100%)}
.hero-arrow{position:absolute;top:178px;width:32px;height:32px;background:rgba(120,120,120,.75);display:flex;align-items:center;justify-content:center}
.hero-title{position:absolute;left:161px;top:221px;font-family:"Roboto Slab",serif;font-size:30px;line-height:43px;color:var(--white);text-shadow:0 2px 6px rgba(0,0,0,.7)}
.estimate-form{position:absolute;left:752px;top:68px;width:289px;height:329px;background:rgba(90,90,90,.55)}
.form-title{position:absolute;left:12px;top:26px;display:flex;align-items:center;gap:8px;font-family:"Roboto Slab",serif;font-size:20px;color:var(--white)}
.form-title span.sq{width:18px;height:18px;background:var(--blue)}
.field{position:absolute;left:17px;width:264px;height:28px;background:var(--field);font-family:"Roboto Condensed",sans-serif;font-size:13px;line-height:14px;color:#333;padding:7px 12px;border-radius:2px}
.submit-row{position:absolute;left:26px;top:287px;width:248px;height:26px}
.submit-row .rule{position:absolute;top:12px;height:1px;background:var(--white)}
.submit-btn{position:absolute;left:91px;top:0;width:63px;height:26px;background:#000;color:var(--white);border-radius:3px;font-family:"Roboto Condensed",sans-serif;font-weight:500;font-size:15px;display:flex;align-items:center;justify-content:center}
.tab{position:absolute;top:352px;height:45px;font-family:"Roboto Slab",serif;font-size:19px;display:flex;align-items:center;padding-left:4px}
.tab-residential{left:160px;width:245px;background:var(--blue);color:var(--white);font-weight:700}
.tab-commercial{left:431px;width:247px;background:rgba(60,60,60,.75);color:var(--white);padding-left:10px}

/* projects */
.projects{position:absolute;left:160px;top:513px;width:881px;height:216px;background:linear-gradient(180deg,#fafafa,#ececec)}
.filter{position:absolute;left:20px;top:20px;font-family:"Vollkorn",serif;font-size:19px;display:flex;align-items:center}
.filter .sep{width:1px;height:24px;background:var(--blue);margin:0 10px}
.filter .active{color:var(--blue)}
.thumb{position:absolute;top:61px;width:155px;height:123px;border:1px solid #333;background:var(--white);padding:4px}
.thumb-img{width:100%;height:100%;position:relative}
.thumb-cap{position:absolute;left:0;bottom:0;width:100%;height:24px;background:rgba(70,70,70,.55);color:var(--white);font-family:"Vollkorn",serif;font-size:15px;padding:2px 7px}

/* welcome */
.welcome{position:absolute;left:0;top:729px;width:1200px;height:215px;background:var(--sky);text-align:center}
.welcome h1{position:absolute;left:0;width:100%;top:26px;font-family:"Vollkorn",serif;font-weight:400;font-size:22px;color:#111}
.welcome-text{position:absolute;left:178px;width:846px;top:87px;font-size:12.5px;line-height:22px;color:#222}
.read-more{position:absolute;left:561px;top:165px;width:78px;height:25px;background:#000;color:var(--white);border-radius:3px;font-size:12.5px;display:flex;align-items:center;justify-content:center}

/* footer */
.site-footer{position:absolute;left:0;top:944px;width:1200px;height:71px;background:var(--footer);border-bottom:4px solid var(--blue)}
.footer-nav{position:absolute;left:165px;top:13px;display:flex;gap:16px;font-size:12.5px;color:#ddd}
.copyright{position:absolute;left:161px;top:35px;font-size:11.5px;color:#eee}
.footer-brand{position:absolute;left:850px;top:17px;display:flex;align-items:center;gap:8px}
.footer-brand .brand-square{width:28px;height:28px;background:#cfcfcf}
.footer-brand .brand-name{font-size:18px;color:#ddd}
</style>
</head>
<body>

<header class="site-header">
  <div class="brand">
    <span class="brand-square"></span>
    <span class="brand-name">BLUEFINCH PAINTING</span>
  </div>
  <div class="estimate-btn">Free Estimates</div>
  <div class="call">
    <svg width="28" height="28" viewBox="0 0 28 28" aria-hidden="true">
      <circle cx="14" cy="14" r="12.5" fill="none" stroke="#1b7fc6" stroke-width="2"/>
      <path d="M11 8c-1.5 1-2 2.5-1.5 4.5 1 3 2.5 5.5 4.5 7 1 .8 2.3.8 3.2 0l.6-.6-2.3-2.4-1.1.7c-1-.8-2-2.5-2.3-3.8l1.1-.6-1-3.3z" fill="#1b7fc6"/>
    </svg>
    <div class="call-text">
      <div class="call-label">Call Us Today</div>
      <div class="call-number">(555) 318-7046</div>
    </div>
  </div>
  <nav class="main-nav">
    <a class="current" href="#">HOME</a>
    <a class="item" href="#">ABOUT US</a>
    <a class="item" href="#">SERVICES</a>
    <a class="item" href="#">PAST PROJECTS</a>
    <a href="#">CONTACT US</a>
  </nav>
</header>

<section class="hero" role="img" aria-label="Photo of a two-storey grey sided house with white windows, a porch and garden shrubs">
  <div class="hero-arrow" style="left:7px">
    <svg width="10" height="12" viewBox="0 0 10 12"><path d="M7 1 2 6l5 5" stroke="#fff" stroke-width="2.5" fill="none"/></svg>
  </div>
  <div class="hero-arrow" style="left:1157px">
    <svg width="10" height="12" viewBox="0 0 10 12"><path d="M3 1l5 5-5 5" stroke="#fff" stroke-width="2.5" fill="none"/></svg>
  </div>
  <h2 class="hero-title">PROVIDING QUALITY WORK AT<br>AFFORDABLE PRICES</h2>

  <form class="estimate-form">
    <div class="form-title"><span class="sq"></span>Free Painting Estimates</div>
    <div class="field" style="top:55px">Name</div>
    <div class="field" style="top:90px">Email</div>
    <div class="field" style="top:125px">Phone</div>
    <div class="field" style="top:160px">Address</div>
    <div class="field" style="top:195px;height:66px">Painting project description</div>
    <div class="submit-row">
      <span class="rule" style="left:0;width:88px"></span>
      <span class="rule" style="left:157px;width:91px"></span>
      <span class="submit-btn">Submit</span>
    </div>
  </form>

  <div class="tab tab-residential">RESIDENTIAL PAINTING</div>
  <div class="tab tab-commercial">COMMERCIAL PAINTING</div>
</section>

<section class="projects">
  <div class="filter"><span>Interior</span><span class="sep"></span><span class="active">Exterior</span></div>
  <div class="thumb" style="left:15px"><div class="thumb-img" role="img" aria-label="Photo of a painted two-storey house with a flower garden" style="background:linear-gradient(180deg,#5b8fd6 0%,#9a8a74 45%,#4f7a3a 100%)"><div class="thumb-cap">Lorem Ispum</div></div></div>
  <div class="thumb" style="left:188px"><div class="thumb-img" role="img" aria-label="Photo of a painter working on a white gable wall" style="background:linear-gradient(135deg,#1f5fb8 0%,#c9ccd2 45%,#e6e6e6 100%)"><div class="thumb-cap">Lorem Ispum</div></div></div>
  <div class="thumb" style="left:361px"><div class="thumb-img" role="img" aria-label="Photo of a painter rolling cream paint on an interior wall" style="background:linear-gradient(180deg,#d8cfa8 0%,#cfc49a 60%,#b9ae86 100%)"><div class="thumb-cap">Lorem Ispum</div></div></div>
  <div class="thumb" style="left:534px"><div class="thumb-img" role="img" aria-label="Photo of a beige stucco home with a green lawn" style="background:linear-gradient(180deg,#8fb4df 0%,#c0ab8c 45%,#4d8a35 100%)"><div class="thumb-cap">Lorem Ispum</div></div></div>
  <div class="thumb" style="left:706px"><div class="thumb-img" role="img" aria-label="Photo of a grey two-storey house with a patio" style="background:linear-gradient(180deg,#7b7d80 0%,#65675f 55%,#3f4a36 100%)"><div class="thumb-cap">Lorem Ispum</div></div></div>
</section>

<section class="welcome">
  <h1>Welcome to Bluefinch Painting</h1>
  <svg class="abs" style="left:437px;top:55px" width="346" height="14" viewBox="0 0 346 14" aria-hidden="true">
    <line x1="0" y1="3" x2="346" y2="3" stroke="#222" stroke-width="1"/>
    <line x1="0" y1="7" x2="346" y2="7" stroke="#222" stroke-width="1"/>
    <path d="M167 1l12 12M179 1l-12 12" stroke="#222" stroke-width="1.2"/>
  </svg>
  <p class="welcome-text">Lorem ipsum dolor sit amet, consectetuer adipiscing elit, sed diam nonummy nibh euismod &nbsp;rent ut laoreet dolore magna aliquam erat volutpat. Ut wisi enim ad minim veniam, quis nostrud lore xererci tation ullamcorper suscipit lobortis nisl ut aliquip ex ea commodo consequat. Duis autem revel eum iriure dolor in hendrerit in vulputate velit esse molestie consequat.</p>
  <svg class="abs" style="left:476px;top:171px" width="248" height="14" viewBox="0 0 248 14" aria-hidden="true">
    <line x1="0" y1="7" x2="248" y2="7" stroke="#fff" stroke-width="1"/>
    <path d="M70 3h16M70 7h16M70 11h16M162 3h16M162 7h16M162 11h16" stroke="#fff" stroke-width="1"/>
  </svg>
  <div class="read-more">Read More</div>
</section>

<footer class="site-footer">
  <nav class="footer-nav">
    <span>• Home</span><span>• About Us</span><span>• Services</span><span>• Past Projects</span><span>• Contact Us</span>
  </nav>
  <div class="copyright">Copyright ©2015, bluefinchpainting.example &nbsp;All Rights Reserved</div>
  <div class="footer-brand">
    <span class="brand-square"></span>
    <span class="brand-name">BLUEFINCH PAINTING</span>
  </div>
</footer>

</body>
</html>
```